Real Estate Business Card

On the front side I want to have my info, my brokerage info.
On the back side I want have my complany’s logo, website and Facebook link. I will provide all this once I select a design.

I would like to see Black background and gold text, Dark Blue and gold text and White and blue text designs

Font styles to use
Sans Serif
Script

```html
<!DOCTYPE html>
<html lang="en">
<head>
<meta charset="utf-8">
<title>Keystone Realty – Business Card</title>
<link href="https://fonts.googleapis.com/css2?family=Roboto:wght@400;500;700;900&display=swap" rel="stylesheet">
<style>
  :root {
    --scene-bg: #2b2b2c;
    --card-bg: #151515;
    --brand-red: #b3262c;
    --brand-silver: #c4c8d2;
    --gold: #c8a44c;
    --text-light: #e6e6e6;
    --rule: #d8d8d8;
  }
  * { box-sizing: border-box; margin: 0; padding: 0; }
  html, body {
    width: 1200px; height: 1017px; overflow: hidden;
    background: var(--scene-bg);
    font-family: "Roboto", Arial, sans-serif;
  }
  .sheet {
    width: 1200px; height: 1017px;
    display: flex; align-items: center; justify-content: center; gap: 56px;
  }
  .card {
    position: relative;
    width: 540px; height: 309px;
    background: var(--card-bg);
    border-radius: 3px;
    box-shadow: 0 18px 40px rgba(0,0,0,.55);
    overflow: hidden;
  }
  .brand {
    display: flex; align-items: center; gap: 10px;
  }
  .brand-mark {
    width: 22px; height: 22px; background: var(--brand-red);
  }
  .brand-name {
    font-weight: 900; color: var(--brand-silver);
    text-transform: uppercase; letter-spacing: .5px; line-height: 1;
  }
  .brand-tag {
    font-size: 9px; letter-spacing: 6px; color: var(--brand-silver);
    text-transform: uppercase; margin-top: 4px; text-align: right;
  }

  /* back side */
  .card--back .brand-block {
    position: absolute; right: 46px; top: 122px;
  }
  .card--back .brand-name { font-size: 34px; }
  .card--back .brand-mark { width: 26px; height: 26px; }

  /* front side */
  .card--front .brand-block {
    position: absolute; right: 38px; top: 34px;
  }
  .card--front .brand-name { font-size: 26px; }
  .divider {
    position: absolute; left: 150px; right: 38px; top: 112px;
    height: 1px; background: var(--rule);
  }
  .office {
    position: absolute; right: 38px; top: 128px;
    text-align: right; color: var(--text-light);
    font-size: 12.5px; line-height: 1.45;
  }
  .person {
    position: absolute; left: 38px; bottom: 30px;
  }
  .person-name {
    color: var(--gold); font-weight: 500; font-size: 19px;
    text-transform: uppercase; letter-spacing: .3px;
  }
  .person-title {
    color: var(--brand-red); font-size: 13px; text-transform: uppercase;
    margin-top: 1px;
  }
  .person-rule {
    width: 165px; height: 1px; background: var(--rule); margin: 8px 0 8px;
  }
  .contact-list { list-style: none; }
  .contact-list li {
    display: flex; align-items: center; gap: 9px;
    color: var(--text-light); font-size: 13px; line-height: 1.55;
  }
  .contact-list svg { width: 12px; height: 12px; flex: none; }
</style>
</head>
<body>
<main class="sheet">

  <section class="card card--back" aria-label="Card back">
    <div class="brand-block">
      <div class="brand">
        <span class="brand-mark"></span>
        <span class="brand-name">Keystone Realty</span>
      </div>
      <div class="brand-tag">Real Estate</div>
    </div>
  </section>

  <section class="card card--front" aria-label="Card front">
    <div class="brand-block">
      <div class="brand">
        <span class="brand-mark"></span>
        <span class="brand-name">Keystone Realty</span>
      </div>
      <div class="brand-tag">Real Estate</div>
    </div>

    <div class="divider"></div>

    <address class="office" style="font-style:normal">
      214 Birchwood Road<br>
      Juneau, Alaska 99801<br>
      www.keystonerealty.com
    </address>

    <div class="person">
      <div class="person-name">Dana Whitlock</div>
      <div class="person-title">CEO/Founder</div>
      <div class="person-rule"></div>
      <ul class="contact-list">
        <li>
          <svg viewBox="0 0 12 12" aria-hidden="true"><path d="M2.5 1 L4.5 1 L5 3.5 L3.8 4.4 C4.5 6 6 7.5 7.6 8.2 L8.5 7 L11 7.5 L11 9.5 C11 10.3 10.3 11 9.5 11 C5 11 1 7 1 2.5 C1 1.7 1.7 1 2.5 1Z" fill="var(--gold)"/></svg>
          555 201 3384
        </li>
        <li>
          <svg viewBox="0 0 12 12" aria-hidden="true"><rect x="3" y="0.8" width="6" height="10.4" rx="1" fill="none" stroke="var(--gold)" stroke-width="1.2"/><circle cx="6" cy="9.4" r=".7" fill="var(--gold)"/></svg>
          555 732 9160
        </li>
        <li>
          <svg viewBox="0 0 12 12" aria-hidden="true"><rect x="1" y="3" width="10" height="7.5" rx="1" fill="var(--gold)"/><rect x="3" y="1" width="6" height="3" fill="none" stroke="var(--gold)" stroke-width="1"/></svg>
          555 418 2675
        </li>
        <li>
          <svg viewBox="0 0 12 12" aria-hidden="true"><rect x="1" y="2.5" width="10" height="7.5" fill="var(--gold)"/><path d="M1.5 3 L6 6.8 L10.5 3" fill="none" stroke="var(--card-bg)" stroke-width="1"/></svg>
          dana@keystonerealty.com
        </li>
      </ul>
    </div>
  </section>

</main>
</body>
</html>
```